Business Card Design Project

Business Card
We are rebranding with a new logo
Industry/Entity Type
Business
Contact Information for Business Card
Dennis Morvale +61 487215963 dennis@quorv.com.au P.O. Box 872 Fernlow QLD 4309
Requirements
Must have
- Logo

```html
<!DOCTYPE html>
<html lang="en">
<head>
<meta charset="utf-8">
<title>Quorv International — Business Card</title>
<link rel="stylesheet" href="https://fonts.googleapis.com/css2?family=Montserrat:wght@500;600;700&display=swap">
<style>
  :root {
    --backdrop: #2b2b2b;
    --card-dark: #1f1f1f;
    --card-light: #f2f2f2;
    --brand-orange: #e9781f;
    --brand-blue: #1f8fc4;
    --brand-blue-deep: #0f5f86;
    --ink: #2e2e2e;
    --ink-soft: #3d3d3d;
  }
  * { box-sizing: border-box; margin: 0; padding: 0; }
  html, body {
    width: 1200px; height: 716px; overflow: hidden;
    background: var(--backdrop);
    font-family: "Montserrat", Arial, sans-serif;
  }
  .stage {
    width: 1200px; height: 716px;
    display: flex; align-items: center; justify-content: center; gap: 60px;
  }
  .card {
    width: 500px; height: 286px; border-radius: 18px;
    position: relative; overflow: hidden;
    box-shadow: 0 10px 24px rgba(0,0,0,.45);
  }
  .card--front {
    background: var(--card-dark);
    display: flex; align-items: center; justify-content: center;
  }
  .brand-name {
    color: var(--brand-orange);
    font-weight: 600;
    letter-spacing: 3px;
    text-transform: uppercase;
  }
  .card--front .brand-name { font-size: 30px; }
  .card--back { background: var(--card-light); }
  .accent-sweep {
    position: absolute; left: 0; top: 0; width: 100%; height: 150px;
  }
  .card--back .brand-name {
    position: absolute; right: 28px; top: 142px;
    font-size: 13px; letter-spacing: 2px;
  }
  .contact {
    position: absolute; left: 236px; top: 176px;
  }
  .contact__name {
    font-size: 21px; font-weight: 600; color: var(--ink);
    margin-bottom: 12px;
  }
  .contact__list { list-style: none; }
  .contact__item {
    display: flex; align-items: center; gap: 8px;
    font-size: 12.5px; font-weight: 500; color: var(--ink-soft);
    line-height: 20px;
  }
  .contact__icon { width: 12px; height: 12px; fill: var(--brand-orange); flex: none; }
</style>
</head>
<body>
<main class="stage">
  <section class="card card--front">
    <span class="brand-name">Quorv International</span>
  </section>

  <section class="card card--back">
    <svg class="accent-sweep" role="img" aria-label="Brand colour sweep in blue and orange" viewBox="0 0 500 150" preserveAspectRatio="none">
      <defs>
        <linearGradient id="sweepFill" x1="0" y1="0" x2="1" y2="0">
          <stop offset="0" stop-color="#e9781f" stop-opacity=".85"/>
          <stop offset=".35" stop-color="#1f8fc4" stop-opacity=".9"/>
          <stop offset="1" stop-color="#1f8fc4" stop-opacity="0"/>
        </linearGradient>
      </defs>
      <rect width="500" height="150" fill="url(#sweepFill)" opacity=".35"/>
    </svg>

    <span class="brand-name">Quorv International</span>

    <div class="contact">
      <p class="contact__name">Dennis Morvale</p>
      <ul class="contact__list">
        <li class="contact__item">
          <svg class="contact__icon" viewBox="0 0 24 24"><path d="M6.6 10.8a15.1 15.1 0 0 0 6.6 6.6l2.2-2.2c.3-.3.7-.4 1-.2 1.1.4 2.3.6 3.6.6.6 0 1 .4 1 1V20c0 .6-.4 1-1 1A17 17 0 0 1 3 4c0-.6.4-1 1-1h3.5c.6 0 1 .4 1 1 0 1.3.2 2.5.6 3.6.1.3 0 .7-.2 1z"/></svg>
          +61 487215963
        </li>
        <li class="contact__item">
          <svg class="contact__icon" viewBox="0 0 24 24"><path d="M2 5h20v14H2z M2 5l10 8 10-8" fill="none" stroke="#e9781f" stroke-width="2.5"/></svg>
          dennis@quorv.com.au
        </li>
        <li class="contact__item">
          <svg class="contact__icon" viewBox="0 0 24 24"><path d="M12 2a7 7 0 0 0-7 7c0 5 7 13 7 13s7-8 7-13a7 7 0 0 0-7-7zm0 9.5A2.5 2.5 0 1 1 12 6.5a2.5 2.5 0 0 1 0 5z"/></svg>
          P.O. Box 872 Fernlow QLD 4309
        </li>
      </ul>
    </div>
  </section>
</main>
</body>
</html>
```